VFX Company Business Card Design Project

The Kestrel Works is a decentralized Visual Effects Studio servicing the television and feature film industries.
Project Brief:
Take our logo that was previously designed on Pencil Harbor and make a double sided business card.
Requirements:
- Card MUST be double sided.
- Front of card MUST have the yellow part of our logo against the dark grey background.
- Back of card is completely up to the designer.
- Back of card must include the complete company logo.
Please follow these File Preparation guidelines:
http://printnook.ca/infopage?file=filetype_en&s=PrintNook_new&lang=en
Business

```html
<!DOCTYPE html>
<html lang="en">
<head>
<meta charset="utf-8">
<title>The Kestrel Works – Business Cards</title>
<link rel="stylesheet" href="https://fonts.googleapis.com/css2?family=Montserrat:wght@300;700&family=Josefin+Sans:wght@400&family=Libre+Baskerville:wght@400;700&display=swap">
<style>
  :root {
    --backdrop: #d9d4cc;
    --card-dark: #262626;
    --card-light: #eaede3;
    --card-slate: #5f6b6d;
    --brand-yellow: #fcc72c;
    --ink-light: #eef0e6;
    --ink-grey: #8a9597;
    --ink-dark: #1f1f1f;
    --ink-white: #ffffff;
  }
  * { margin: 0; padding: 0; box-sizing: border-box; }
  html, body {
    width: 1200px; height: 734px; overflow: hidden;
    background: var(--backdrop);
  }
  .sheet { position: relative; width: 1200px; height: 734px; }

  .card {
    position: absolute;
    width: 524px; height: 299px;
    border-radius: 24px;
    box-shadow: 0 2px 6px rgba(0,0,0,0.25);
  }
  .card--front      { left: 67px;  top: 43px;  background: var(--card-dark); }
  .card--contact    { left: 628px; top: 47px;  background: var(--card-dark); border-radius: 18px; }
  .card--light-back { left: 64px;  top: 384px; background: var(--card-light); }
  .card--slate-back { left: 622px; top: 388px; background: var(--card-slate); }

  .brand-name {
    font-family: "Montserrat", sans-serif;
    font-weight: 700;
    white-space: nowrap;
    line-height: 1;
  }
  .tagline {
    font-family: "Montserrat", sans-serif;
    font-weight: 300;
    text-transform: uppercase;
    letter-spacing: 0.32em;
    white-space: nowrap;
    line-height: 1;
  }
  .web-address {
    position: absolute; left: 0; right: 0;
    text-align: center;
    font-family: "Josefin Sans", sans-serif;
    font-size: 17px;
    letter-spacing: 0.14em;
  }

  /* Front */
  .card--front .brand-name {
    position: absolute; left: 0; right: 0; top: 126px;
    text-align: center;
    font-size: 50px;
    color: var(--brand-yellow);
  }

  /* Contact side */
  .card--contact .brand-name {
    position: absolute; left: 48px; top: 50px;
    font-size: 46px;
    color: var(--ink-light);
  }
  .card--contact .tagline {
    position: absolute; left: 80px; top: 112px;
    font-size: 25px;
    color: var(--ink-grey);
  }
  .address {
    position: absolute; left: 0; right: 0; top: 174px;
    text-align: center;
    font-family: "Libre Baskerville", serif;
    font-size: 13px;
    letter-spacing: 0.08em;
    color: var(--ink-light);
  }
  .person {
    position: absolute; right: 310px; top: 227px;
    text-align: right;
    font-family: "Libre Baskerville", serif;
    color: var(--ink-light);
  }
  .person__name  { font-size: 18px; font-weight: 700; }
  .person__title { font-size: 13px; margin-top: 4px; }
  .divider {
    position: absolute; left: 227px; top: 210px;
    width: 1px; height: 62px;
    background: var(--ink-light);
  }
  .contact-list {
    position: absolute; left: 242px; top: 209px;
    list-style: none;
    font-family: "Libre Baskerville", serif;
    font-size: 12.5px;
    color: var(--ink-light);
  }
  .contact-list li { display: flex; align-items: center; height: 19.5px; gap: 5px; }
  .contact-list svg { width: 10px; height: 10px; fill: var(--ink-light); }

  /* Light back */
  .card--light-back .brand-name {
    position: absolute; left: 0; right: 0; top: 112px;
    text-align: center;
    font-size: 46px;
    color: var(--ink-dark);
  }
  .card--light-back .tagline {
    position: absolute; left: 0; right: 0; top: 168px;
    text-align: center;
    font-size: 17px;
    color: var(--ink-dark);
  }
  .card--light-back .web-address { top: 256px; color: var(--ink-dark); }

  /* Slate back */
  .card--slate-back .brand-name {
    position: absolute; left: 0; right: 0; top: 102px;
    text-align: center;
    font-size: 48px;
    color: var(--ink-white);
  }
  .card--slate-back .tagline {
    position: absolute; left: 0; right: 0; top: 164px;
    text-align: center;
    font-size: 23px;
    color: var(--ink-white);
  }
  .card--slate-back .web-address { top: 258px; color: var(--ink-white); }
</style>
</head>
<body>
<main class="sheet">

  <section class="card card--front">
    <div class="brand-name">The Kestrel Works</div>
  </section>

  <section class="card card--contact">
    <div class="brand-name">The Kestrel Works</div>
    <div class="tagline">Virtual Studio</div>
    <p class="address">00, Complex name, City, State 0042</p>
    <div class="person">
      <div class="person__name">Your Name</div>
      <div class="person__title">Title</div>
    </div>
    <div class="divider"></div>
    <ul class="contact-list">
      <li>
        <svg viewBox="0 0 10 10" aria-hidden="true"><path d="M2 0.5 L3.6 2.6 L2.6 3.6 Q3.6 5.8 6.4 7.4 L7.4 6.4 L9.5 8 L8.2 9.5 Q1 8 0.5 1.8 Z"/></svg>
        0987 654321
      </li>
      <li>
        <svg viewBox="0 0 10 10" aria-hidden="true"><path d="M3 0.5 H7 Q8 0.5 8 1.5 V8.5 Q8 9.5 7 9.5 H3 Q2 9.5 2 8.5 V1.5 Q2 0.5 3 0.5 Z M3 1.8 V7.4 H7 V1.8 Z"/></svg>
        0987 654321
      </li>
      <li>
        <svg viewBox="0 0 10 10" aria-hidden="true"><path d="M0.5 2 H9.5 V8.5 H0.5 Z M1.3 2.8 L5 5.6 L8.7 2.8 Z" fill-rule="evenodd"/></svg>
        info@kestrelworks.com
      </li>
      <li>
        <svg viewBox="0 0 10 10" aria-hidden="true"><circle cx="5" cy="5" r="4.3" fill="none" stroke="currentColor" stroke-width="1" style="stroke:var(--ink-light)"/><path d="M0.7 5 H9.3 M5 0.7 Q2.6 5 5 9.3 Q7.4 5 5 0.7" fill="none" style="stroke:var(--ink-light)" stroke-width="0.8"/></svg>
        www.kestrelworks.com
      </li>
    </ul>
  </section>

  <section class="card card--light-back">
    <div class="brand-name">The Kestrel Works</div>
    <div class="tagline">Virtual Studio</div>
    <p class="web-address">www.kestrelworks.com</p>
  </section>

  <section class="card card--slate-back">
    <div class="brand-name">The Kestrel Works</div>
    <div class="tagline">Virtual Studio</div>
    <p class="web-address">www.kestrelworks.com</p>
  </section>

</main>
</body>
</html>
```